Storm Restoration Contractor needs a professional letterhead design

Looking for a professional letterhead design. Not looking for your cheapo MS Word standard ones that are readily available. Dont want it to be cookie cutter look like ones readily available online. We just recently changed our logo and want to freshen up all our documents. Our company handles restoring a property back to a pre-loss condition after a storm damages it. For example, wind, hail, flood, fire losses.

Target Market(s)

Property Owners, Homeowners, Property Owners, Commercial Property Owners, Property Management Companies

Industry/Entity Type

Construction Company

Requirements
Must have
• Professional, Use 1 of 2 logo options
• Storm Restoration, Roofing, Siding, Windows

```html
<!DOCTYPE html>
<html lang="en">
<head>
<meta charset="utf-8">
<title>Stormline Exteriors Letterhead</title>
<link rel="stylesheet" href="https://fonts.googleapis.com/css2?family=Open+Sans:wght@400;600;700&display=swap">
<style>
  :root {
    --backdrop: #e6e6e6;
    --paper: #ffffff;
    --brand-blue: #1f73bd;
    --ink: #3a3a3a;
    --ink-soft: #555555;
    --rule: #9a9a9a;
    --band-edge: #4a4f57;
    --sig-light: #f2f2f2;
    --sig-dark: #e4e4e4;
  }
  html, body {
    margin: 0;
    width: 1200px;
    height: 936px;
    overflow: hidden;
    background: var(--backdrop);
    font-family: "Open Sans", Arial, sans-serif;
  }
  .letterhead {
    position: absolute;
    left: 289px;
    top: 28px;
    width: 622px;
    height: 880px;
    background: var(--paper);
    box-shadow: 0 4px 18px rgba(0,0,0,.12);
    overflow: hidden;
  }
  .brand {
    position: absolute;
    left: 52px;
    top: 56px;
    display: flex;
    align-items: center;
    gap: 10px;
  }
  .brand-dot {
    width: 30px;
    height: 30px;
    border-radius: 50%;
    background: var(--brand-blue);
  }
  .brand-name {
    font-size: 15px;
    font-weight: 700;
    color: var(--brand-blue);
    letter-spacing: .04em;
    text-transform: uppercase;
  }
  .header-rule {
    position: absolute;
    left: 52px;
    right: 52px;
    top: 112px;
    border-top: 1px solid var(--rule);
  }
  .letter {
    position: absolute;
    left: 52px;
    right: 52px;
    top: 300px;
    color: var(--ink-soft);
    font-size: 10.5px;
    line-height: 1.45;
  }
  .salutation {
    font-size: 13px;
    font-weight: 700;
    color: var(--ink);
    margin: 0 0 8px;
  }
  .letter p { margin: 0 0 14px; }
  .signature {
    position: absolute;
    left: 52px;
    top: 560px;
    width: 130px;
    height: 46px;
    background: linear-gradient(90deg, var(--sig-light), var(--sig-dark));
  }
  .contact {
    position: absolute;
    right: 52px;
    top: 700px;
    text-align: right;
    font-style: normal;
    font-size: 10.5px;
    line-height: 1.5;
    color: var(--ink);
  }
  .contact-name {
    font-weight: 700;
    font-size: 12px;
    color: var(--brand-blue);
  }
  .contact b { color: var(--brand-blue); }
  .service-band {
    position: absolute;
    left: 0;
    right: 0;
    bottom: 0;
    height: 66px;
    background: var(--brand-blue);
    border-top: 4px solid var(--band-edge);
    display: flex;
    align-items: flex-start;
    justify-content: flex-end;
    padding: 16px 52px 0 0;
    box-sizing: border-box;
    color: #fff;
    font-size: 12px;
    letter-spacing: .18em;
  }
</style>
</head>
<body>
  <main class="letterhead">
    <div class="brand">
      <span class="brand-dot"></span>
      <span class="brand-name">Stormline Exteriors</span>
    </div>
    <div class="header-rule"></div>

    <section class="letter">
      <p class="salutation">Dear Mr. Carter,</p>
      <p>Lorem Ipsum is simply dummy text of the printing and typesetting industry. Lorem Ipsum has been the industry's standard dummy text ever since the 1500s, when an unknown printer took a galley of type and scrambled it to make a type specimen book. It has survived not only five centuries, but also the leap into electronic typesetting, remaining essentially unchanged.</p>
      <p>The standard chunk of Lorem Ipsum used since the 1500s is reproduced below for those interested. Sections 1.10.32 and 1.10.33 from "de Finibus Bonorum et Malorum" by Cicero are also reproduced in their exact original form, accompanied by English versions from the 1914 translation.</p>
      <p>Lorem Ipsum is simply dummy text of the printing and typesetting industry. Lorem Ipsum has been the industry's standard dummy text ever since the 1500s, when an unknown printer took a galley of type and scrambled it to make a type specimen book. It has survived not only five centuries, but also the leap into electronic typesetting, remaining essentially unchanged.</p>
    </section>

    <div class="signature" role="img" aria-label="Handwritten signature of the sender"></div>

    <address class="contact">
      <div class="contact-name">Stormline Exteriors</div>
      <div><b>P:</b> 555-014-2866 | <b>F:</b> 555-014-1568 | <b>E:</b> info@stormlineexteriors.com</div>
      <div>www.stormlineexteriors.com</div>
    </address>

    <footer class="service-band">STORM RESTORATION | ROOFING | SIDING | WINDOWS</footer>
  </main>
</body>
</html>
```